Modern design company business card design

We are a design oriented construction firm. The owner is an architect and licensed General Contractor and accomplished furniture designer. We do new home construction and large scale remodeling and office design. We would like a design for our new business cards that is clean and modern, but relatable. We like the bright green color of our logo mixed with different shades of grey. We're also open to reinterpreting the logo.

Target Market(s)

Potential design clients,
Construction clients

Industry/Entity Type

Architecture

Contact Information for Business Card

Tall Maple Design | Build Inc. (optional with logo, Inc. optional)Jeffrey MorganOwner (optional)317.555.0148 cell317.431.8056 officejmorgan@greensquareinc.comwww.greensquareinc.com

Font styles to use
Sans Serif
Other font styles liked:
• Avenir

Requirements
Nice to have
• I like designs that have some continuity between the front and back, i.e. similar layouts or graphic elements that wrap around the card. I tend to prefer horizontal over vertical, but that's not a have to. I also tend to prefer white or recycled paper.

```html
<!DOCTYPE html>
<html lang="en">
<head>
<meta charset="utf-8">
<title>Tall Maple Design | Build – Business Card</title>
<link rel="stylesheet" href="https://fonts.googleapis.com/css2?family=Nunito+Sans:wght@300;400;700&display=swap">
<style>
  :root {
    --backdrop: #3b3431;
    --card: #141414;
    --card-edge: #1d1d1d;
    --accent: #9bd23c;
    --name-grey: #8a8a8a;
    --text-white: #f2f2f2;
    --text-soft: #d6d6d6;
  }
  * { box-sizing: border-box; margin: 0; padding: 0; }
  html, body {
    width: 1200px;
    height: 844px;
    overflow: hidden;
    background: var(--backdrop);
    font-family: "Nunito Sans", "Helvetica Neue", Arial, sans-serif;
  }
  .stage {
    position: relative;
    width: 1200px;
    height: 844px;
  }
  .card {
    position: absolute;
    top: 268px;
    width: 540px;
    height: 309px;
    background: var(--card);
    border: 1px solid var(--card-edge);
    box-shadow: 0 10px 30px rgba(0, 0, 0, 0.45);
  }
  .card--front { left: 50px; }
  .card--back { left: 610px; }

  .company {
    position: absolute;
    display: flex;
    align-items: center;
    gap: 14px;
    white-space: nowrap;
  }
  .company__dot {
    width: 26px;
    height: 26px;
    flex: none;
    border-radius: 50%;
    background: var(--accent);
  }
  .company__name {
    color: var(--name-grey);
    font-weight: 300;
    font-size: 22px;
    letter-spacing: 0.5px;
    line-height: 1;
  }

  .card--front .company { left: 60px; top: 112px; }
  .card--back .company {
    left: 0;
    right: 0;
    top: 141px;
    justify-content: center;
  }

  .owner {
    position: absolute;
    left: 80px;
    width: 190px;
    top: 226px;
    text-align: right;
  }
  .owner__name {
    color: var(--accent);
    font-weight: 700;
    font-size: 17px;
  }
  .owner__title {
    color: var(--text-soft);
    font-size: 13px;
  }

  .contact-list {
    position: absolute;
    left: 298px;
    top: 196px;
    list-style: none;
  }
  .contact-list__item {
    display: flex;
    align-items: center;
    gap: 9px;
    height: 19px;
    color: var(--text-white);
    font-size: 13px;
    letter-spacing: 0.2px;
  }
  .contact-list__icon {
    width: 11px;
    height: 11px;
    flex: none;
    fill: none;
    stroke: var(--accent);
    stroke-width: 1.6;
    stroke-linecap: round;
    stroke-linejoin: round;
  }
</style>
</head>
<body>
<main class="stage">

  <section class="card card--front" aria-label="Business card front">
    <div class="company">
      <span class="company__dot" aria-hidden="true"></span>
      <span class="company__name">Tall Maple Design | Build Inc.</span>
    </div>

    <div class="owner">
      <div class="owner__name">Dennis Holloway</div>
      <div class="owner__title">Owner</div>
    </div>

    <ul class="contact-list">
      <li class="contact-list__item">
        <svg class="contact-list__icon" viewBox="0 0 12 12" aria-hidden="true"><path d="M2.5 1.5 L4.5 1.5 L5.2 3.8 L4 4.8 C4.7 6.3 5.7 7.3 7.2 8 L8.2 6.8 L10.5 7.5 L10.5 9.5 C10.5 10 10 10.5 9.5 10.5 C5.3 10.3 1.7 6.7 1.5 2.5 C1.5 2 2 1.5 2.5 1.5 Z"/></svg>
        <span>317.555.0172</span>
      </li>
      <li class="contact-list__item">
        <svg class="contact-list__icon" viewBox="0 0 12 12" aria-hidden="true"><rect x="3" y="1" width="6" height="10" rx="1"/><line x1="5.5" y1="9" x2="6.5" y2="9"/></svg>
        <span>317.555.0148</span>
      </li>
      <li class="contact-list__item">
        <svg class="contact-list__icon" viewBox="0 0 12 12" aria-hidden="true"><rect x="1" y="2.5" width="10" height="7"/><polyline points="1,2.5 6,6.5 11,2.5"/></svg>
        <span>dholloway@tallmapleinc.example</span>
      </li>
      <li class="contact-list__item">
        <svg class="contact-list__icon" viewBox="0 0 12 12" aria-hidden="true"><path d="M5 7 L7 5"/><path d="M6.2 3.2 L7.4 2 C8.2 1.2 9.5 1.2 10.2 2 C11 2.7 11 4 10.2 4.8 L9 6"/><path d="M5.8 8.8 L4.6 10 C3.8 10.8 2.5 10.8 1.8 10 C1 9.3 1 8 1.8 7.2 L3 6"/></svg>
        <span>www.tallmapleinc.example</span>
      </li>
    </ul>
  </section>

  <section class="card card--back" aria-label="Business card back">
    <div class="company">
      <span class="company__dot" aria-hidden="true"></span>
      <span class="company__name">Tall Maple Design | Build Inc.</span>
    </div>
  </section>

</main>
</body>
</html>
```